Varnik Holdings — Business Card Design Brief
Overview
Design a double-sided business card for Varnik Holdings that highlights our two service arms: Varnik Communications (telecommunications) and Varnik Energy (business energy solutions). The card should feel smart and stand out when handed to clients.

Objectives
Showcase our areas of specialty clearly.
Reflect the overall Varnik / Varnik Holdings brand while acknowledging both arms.
Explore using both logos (Communications + Energy) or one unified logo, depending on the design.

Deliverables
One double-sided business card design (front + back).

Content & Copy
Front (preferred): Logo: Varnik / Varnik Holdings
Descriptor: Business Communications | Business Energy
Back:My contact details and company details
Core products: Business Mobile • Telephony • Internet • Business Energy Solutions

Brand & Visual Direction
We have a group logo currently tailored more toward telecoms, plus a separate Varnik Energy logo.
Please explore layouts that use both logos or just one, whichever works best.
Color: I wouldn't mind seeing an option using our the Blue/Purple gradient from our website (varnik-example.co.uk), but also open to non-gradient approaches and other colours..

Overall look: Smart, modern, and distinctive.
Format & Print Specs
Double-sided business card format. (Use a standard size

Must-Haves
Front: Varnik wording or Varnik Holdings wording with atleast 1 logo also on front “Business Communications | Business Energy.”

Back: Contact + company details and core products.
A design that stands out while remaining professional.

Nice-to-Have Options
A gradient version using our site’s Blue/Purple gradient.
A non-gradient version.
A dual-logo treatment versus a single-logo treatment.

Thanks
Owen

```html
<!DOCTYPE html>
<html lang="en">
<head>
<meta charset="utf-8">
<title>Varnik Holdings — Business Card</title>
<link rel="stylesheet" href="https://fonts.googleapis.com/css2?family=Montserrat:wght@500;600;700;800&display=swap">
<style>
  :root {
    --stage: #b9b9b9;
    --card-white: #ffffff;
    --navy: #1e1f5e;
    --ink: #26273a;
    --accent-blue: #1d9ad6;
    --accent-dot: #1aa3dc;
    --faint-ring: #e6eef7;
    --grad-purple: #7a4a9e;
    --grad-blue: #1763a6;
    --divider-green: #5aa63a;
    --energy-green: #4cb04a;
    --white: #ffffff;
  }
  * { margin: 0; padding: 0; box-sizing: border-box; }
  html, body { width: 1200px; height: 802px; overflow: hidden; }
  body {
    background: var(--stage);
    font-family: "Montserrat", sans-serif;
    position: relative;
  }
  .card {
    position: absolute;
    top: 241px;
    width: 560px;
    height: 320px;
    border-radius: 22px;
    overflow: hidden;
    box-shadow: 0 10px 30px rgba(0,0,0,.18);
  }

  /* Contact side */
  .card-contact { left: 27px; background: var(--card-white); color: var(--ink); }
  .card-contact .faint-ring {
    position: absolute; right: -40px; top: -60px;
    width: 300px; height: 300px; border-radius: 50%;
    border: 26px solid var(--faint-ring);
  }
  .card-contact .wordmark {
    position: absolute; left: 40px; top: 34px;
    font-size: 58px; font-weight: 800; letter-spacing: 1px;
    color: var(--navy);
  }
  .card-contact .accent-bar {
    position: absolute; left: 0; top: 122px;
    width: 22px; height: 44px; background: var(--accent-blue);
  }
  .person { position: absolute; left: 40px; top: 118px; }
  .person .name { font-size: 19px; font-weight: 800; color: var(--navy); letter-spacing: .5px; }
  .person .role { font-size: 13px; font-weight: 500; margin-top: 2px; }
  .address { position: absolute; left: 40px; top: 172px; font-size: 13px; font-weight: 500; line-height: 1.35; }
  .contacts { position: absolute; left: 40px; top: 216px; list-style: none; font-size: 13px; font-weight: 500; line-height: 1.45; }
  .contacts li { display: flex; align-items: center; gap: 7px; }
  .contacts svg { width: 11px; height: 11px; fill: var(--accent-dot); }
  .products {
    position: absolute; left: 40px; bottom: 22px;
    font-size: 13px; font-weight: 500;
  }
  .products .dot { color: var(--accent-dot); margin: 0 4px; }

  /* Brand side */
  .card-brand {
    left: 613px;
    background: linear-gradient(115deg, var(--grad-purple) 0%, #4f58a0 50%, var(--grad-blue) 100%);
    color: var(--white);
  }
  .arm {
    position: absolute; top: 0; bottom: 0; width: 280px;
    display: flex; flex-direction: column; align-items: center; justify-content: center;
  }
  .arm-communications { left: 0; }
  .arm-energy { right: 0; }
  .arm .lockup { display: flex; align-items: center; gap: 12px; }
  .arm .mark-dot { width: 30px; height: 30px; border-radius: 50%; }
  .arm-communications .mark-dot { background: var(--accent-blue); }
  .arm-energy .mark-dot { background: var(--energy-green); }
  .arm .name { font-size: 44px; font-weight: 800; letter-spacing: 1px; }
  .arm .descriptor { margin-top: 22px; font-size: 15px; font-weight: 700; letter-spacing: .4px; }
  .card-brand .divider {
    position: absolute; left: 279px; top: 90px; width: 1.5px; height: 140px;
    background: var(--divider-green);
  }
</style>
</head>
<body>

<section class="card card-contact" aria-label="Contact side">
  <div class="faint-ring"></div>
  <div class="wordmark">VARNIK</div>
  <div class="accent-bar"></div>
  <div class="person">
    <p class="name">DANIEL ASHWORTH</p>
    <p class="role">Founder/CEO</p>
  </div>
  <p class="address">27 Calder Row, Leeds<br>England, LS2 9QT</p>
  <ul class="contacts">
    <li><svg viewBox="0 0 24 24"><path d="M6.6 10.8a15 15 0 0 0 6.6 6.6l2.2-2.2c.3-.3.7-.4 1-.2 1.1.4 2.3.6 3.6.6.6 0 1 .4 1 1V20c0 .6-.4 1-1 1A17 17 0 0 1 3 4c0-.6.4-1 1-1h3.5c.6 0 1 .4 1 1 0 1.3.2 2.5.6 3.6.1.3 0 .7-.2 1z"/></svg>+44 0113 496 0872</li>
    <li><svg viewBox="0 0 24 24"><path d="M2 5h20v14H2zm2 2v.5l8 5 8-5V7z"/></svg>info@varnik-example.co.uk</li>
    <li><svg viewBox="0 0 24 24"><path d="M12 2a10 10 0 1 0 0 20 10 10 0 0 0 0-20zm6.9 6h-3a15 15 0 0 0-1.3-4A8 8 0 0 1 18.9 8zM12 4c.8 1.2 1.5 2.5 1.9 4h-3.8c.4-1.5 1.1-2.8 1.9-4zM4.3 14a8 8 0 0 1 0-4h3.4a16 16 0 0 0 0 4zm.8 2h3a15 15 0 0 0 1.3 4A8 8 0 0 1 5.1 16zM8 8H5.1a8 8 0 0 1 4.3-4C8.8 5.3 8.4 6.6 8 8zm4 12c-.8-1.2-1.5-2.5-1.9-4h3.8c-.4 1.5-1.1 2.8-1.9 4zm2.3-6H9.7a14 14 0 0 1 0-4h4.6a14 14 0 0 1 0 4zm.3 6c.6-1.2 1-2.6 1.3-4h3a8 8 0 0 1-4.3 4zm1.7-6a16 16 0 0 0 0-4h3.4a8 8 0 0 1 0 4z"/></svg>www.varnik-example.co.uk</li>
  </ul>
  <p class="products">Business Mobile<span class="dot">•</span>Telephony<span class="dot">•</span>Internet<span class="dot">•</span>Business Energy Solutions</p>
</section>

<section class="card card-brand" aria-label="Brand side">
  <div class="arm arm-communications">
    <div class="lockup"><span class="mark-dot"></span><span class="name">VARNIK</span></div>
    <p class="descriptor">Business Communications</p>
  </div>
  <div class="divider"></div>
  <div class="arm arm-energy">
    <div class="lockup"><span class="mark-dot"></span><span class="name">VARNIK</span></div>
    <p class="descriptor">Business Energy</p>
  </div>
</section>

</body>
</html>
```